holloway paving service

Needs to have phone number 0418259730 and email markholloway@brightmail.com.au.
ABN 62318470915
name mark holloway

For all your concreting solutions
Excavation
Exposed & colour concrete
House & shed slabs
Driveways
Landing & steps

Contact Information for Business Card

ph 0418259730
email markholloway@brightmail.com.au.
ABN 62318470915
name mark holloway

```html
<!DOCTYPE html>
<html lang="en">
<head>
<meta charset="utf-8">
<title>Holloway Paving Service – Business Card</title>
<link href="https://fonts.googleapis.com/css2?family=Roboto:wght@400;500&family=Roboto+Condensed:wght@500&display=swap" rel="stylesheet">
<style>
  :root {
    --orange: #f26a21;
    --paper: #f4f4f3;
    --ink: #3d3d3d;
    --rule: #555555;
    --backdrop: #2b2b2b;
    --white: #ffffff;
  }
  html, body {
    margin: 0;
    padding: 0;
    width: 1200px;
    height: 960px;
    overflow: hidden;
    background: var(--backdrop);
    font-family: "Roboto", Arial, sans-serif;
  }
  .canvas {
    position: relative;
    width: 1200px;
    height: 960px;
  }
  .card {
    position: absolute;
    width: 600px;
    height: 342px;
    box-sizing: border-box;
  }
  /* Front side */
  .card--front {
    left: 321px;
    top: 110px;
    background: var(--paper);
    border-bottom: 10px solid var(--orange);
    box-shadow: inset 0 -3px 0 #d8d8d8;
  }
  .brand {
    position: absolute;
    right: 38px;
    top: 40px;
    display: flex;
    align-items: center;
    gap: 14px;
  }
  .brand__mark {
    width: 18px;
    height: 18px;
    background: var(--orange);
  }
  .brand__text {
    border-left: 2px solid var(--orange);
    padding-left: 10px;
    height: 82px;
    display: flex;
    flex-direction: column;
    justify-content: center;
  }
  .brand__name {
    color: var(--orange);
    font-weight: 500;
    font-size: 16px;
    letter-spacing: 0.5px;
    line-height: 1.2;
    text-transform: uppercase;
  }
  .brand__phone {
    color: var(--orange);
    font-size: 13px;
    letter-spacing: 1.5px;
    margin-top: 2px;
  }
  .person {
    position: absolute;
    left: 28px;
    top: 218px;
    width: 535px;
  }
  .person__name {
    margin: 0;
    color: var(--orange);
    font-family: "Roboto Condensed", Arial, sans-serif;
    font-weight: 500;
    font-size: 23px;
    text-transform: uppercase;
    padding-bottom: 6px;
    border-bottom: 1px solid var(--rule);
  }
  .contact {
    list-style: none;
    margin: 10px 0 0;
    padding: 0;
  }
  .contact li {
    display: flex;
    align-items: center;
    gap: 8px;
    font-size: 14px;
    color: var(--ink);
    height: 19px;
  }
  .contact svg { width: 13px; height: 13px; flex: none; }
  .abn {
    position: absolute;
    right: 36px;
    top: 302px;
    font-size: 14px;
    color: var(--ink);
  }
  /* Back side */
  .card--back {
    left: 320px;
    top: 493px;
    background: var(--orange);
    color: var(--white);
    text-align: center;
  }
  .back-brand {
    position: absolute;
    left: 0;
    right: 0;
    top: 140px;
    display: flex;
    justify-content: center;
    align-items: center;
    gap: 12px;
  }
  .back-brand__mark {
    width: 22px;
    height: 22px;
    background: var(--white);
  }
  .back-brand__name {
    font-weight: 500;
    font-size: 28px;
    letter-spacing: 1px;
    text-transform: uppercase;
  }
  .services {
    position: absolute;
    left: 0;
    right: 0;
    top: 271px;
    font-size: 14.5px;
    line-height: 18px;
  }
  .services p { margin: 0; }
  .sep { font-size: 9px; vertical-align: 2px; margin: 0 4px; }
</style>
</head>
<body>
<div class="canvas">
  <section class="card card--front">
    <div class="brand">
      <div class="brand__mark"></div>
      <div class="brand__text">
        <div class="brand__name">Holloway Paving Service</div>
        <div class="brand__phone">0418259730</div>
      </div>
    </div>

    <div class="person">
      <h1 class="person__name">Mark Holloway</h1>
      <ul class="contact">
        <li>
          <svg viewBox="0 0 16 16" aria-hidden="true"><path fill="#f26a21" d="M3.6 1.2l2.3 2.6-1.3 1.8c.9 2 2.6 3.7 4.6 4.6l1.8-1.3 2.6 2.3-1.4 2.2C7.2 13.6 2.4 8.8 1.4 3.8z"/></svg>
          0418259730
        </li>
        <li>
          <svg viewBox="0 0 16 16" aria-hidden="true"><rect x="1" y="3" width="14" height="10" fill="#f26a21"/><path d="M1.5 3.8L8 9l6.5-5.2" stroke="#fff" stroke-width="1.4" fill="none"/></svg>
          markholloway@brightmail.com.au
        </li>
        <li>
          <svg viewBox="0 0 16 16" aria-hidden="true"><circle cx="8" cy="8" r="7" fill="#f26a21"/><path d="M8 1v14M1 8h14M3 4.5h10M3 11.5h10" stroke="#fff" stroke-width="1" fill="none"/><ellipse cx="8" cy="8" rx="3" ry="7" stroke="#fff" stroke-width="1" fill="none"/></svg>
          www.hollowaypaving.com.au
        </li>
      </ul>
    </div>
    <div class="abn">ABN 62318470915</div>
  </section>

  <section class="card card--back">
    <div class="back-brand">
      <div class="back-brand__mark"></div>
      <div class="back-brand__name">Holloway Paving Service</div>
    </div>
    <div class="services">
      <p>Excavation<span class="sep">◆</span>Exposed &amp; colour concrete</p>
      <p>House &amp; shed slabs<span class="sep">◆</span>Driveways<span class="sep">◆</span>Landing &amp; steps</p>
    </div>
  </section>
</div>
</body>
</html>
```